Heritage Hollow Business Cards

Require a business card design. <br/><br/>Needs to include logo (either round or long version) plus these details:<br/>Maya Torvell<br/>Heritage Hollow<br/>maya@kelvadtrading.com.au<br/>02 6481 7395<br/>PO Box Glenwarra NSW 2791<br/>www.heritagehollow.com.au<br/><br/>I need in an editable format so that I can create for multiple staff members. <br/><br/>

Target Market(s)

We are an online store selling renovation products to home owners are builders. Looking for a classic classy design.

Industry/Entity Type

Home And Garden

Contact Information for Business Card

Maya Torvell
Heritage Hollow
maya@kelvadtrading.com.au
02 6481 7395
PO Box Glenwarra NSW 2791
www.heritagehollow.com.au

Colors

Designer to choose colors to be used in the design.

Requirements
Must have
• Must include Logo.

```html
<!DOCTYPE html>
<html lang="en">
<head>
<meta charset="utf-8">
<title>Heritage Hollow Business Cards</title>
<link rel="stylesheet" href="https://fonts.googleapis.com/css2?family=Montserrat:wght@300;400;600;700&display=swap">
<style>
  :root {
    --backdrop: #2a2a2a;
    --card-black: #0a0a0a;
    --card-white: #ffffff;
    --ink: #141414;
    --swoosh: #231f1f;
    --sage: #4f6b5d;
    --address: #36443d;
    --light: #f4f4f2;
    --ring-dark: #d9d9d9;
    --ring-light: #3a3a3a;
  }
  * { margin: 0; padding: 0; box-sizing: border-box; }
  html, body {
    width: 1200px; height: 900px; overflow: hidden;
    background: var(--backdrop);
    font-family: "Montserrat", sans-serif;
  }
  .sheet {
    position: relative; width: 1200px; height: 900px;
    display: flex; flex-direction: column; align-items: center;
    justify-content: center; gap: 24px;
  }
  .card {
    position: relative; width: 700px; height: 400px; overflow: hidden;
    box-shadow: 0 10px 30px rgba(0,0,0,.45);
  }
  .card--front { background: var(--card-black); }
  .card--back { background: var(--card-white); }

  .brand-mark {
    position: absolute; border-radius: 50%;
    display: flex; align-items: center; justify-content: center;
    text-align: center; font-weight: 600; line-height: 1.05;
  }
  .card--front .brand-mark {
    width: 230px; height: 230px; left: 300px; top: 85px;
    border: 1.5px solid var(--ring-dark);
    color: var(--light); font-size: 36px;
  }
  .card--back .brand-mark {
    width: 200px; height: 200px; left: 38px; top: 28px;
    border: 1.5px solid var(--ring-light);
    color: var(--ink); font-size: 31px;
  }

  .holder-name {
    position: absolute; right: 48px; top: 112px; z-index: 2;
    font-size: 32px; font-weight: 700; color: var(--ink); letter-spacing: .5px;
    line-height: 1.2;
  }
  .wave { position: absolute; left: 0; top: 0; z-index: 1; }

  .contact {
    position: absolute; right: 48px; top: 250px; z-index: 2;
    text-align: right; font-weight: 300; font-size: 19px; line-height: 1.28;
    font-style: normal;
  }
  .contact__address { color: var(--address); margin-bottom: 8px; }
  .contact__line {
    display: flex; justify-content: flex-end; align-items: center; gap: 8px;
    color: var(--light);
  }
  .contact__icon { width: 19px; height: 19px; flex: none; }
</style>
</head>
<body>
<main class="sheet">
  <section class="card card--front">
    <div class="brand-mark">Heritage<br>Hollow</div>
  </section>

  <section class="card card--back">
    <div class="brand-mark">Heritage<br>Hollow</div>
    <h1 class="holder-name">Maya Torvell</h1>

    <svg class="wave" width="700" height="400" viewBox="0 0 700 400" aria-hidden="true">
      <path d="M0 305 C 150 280, 260 240, 380 207 C 480 180, 590 176, 700 200 L700 222 C 600 201, 490 206, 390 236 C 270 272, 150 305, 0 328 Z" fill="var(--swoosh)"/>
      <path d="M0 350 C 150 330, 270 296, 390 259 C 490 229, 600 222, 700 234 L700 400 L0 400 Z" fill="var(--sage)"/>
    </svg>

    <address class="contact">
      <div class="contact__address">PO Box Glenwarra<br>NSW 2791</div>
      <div class="contact__line">02 6481 7395
        <svg class="contact__icon" viewBox="0 0 20 20"><circle cx="10" cy="10" r="8.5" fill="none" stroke="currentColor" stroke-width="1.4"/><path d="M7 6 l1.5 0 l0.8 2.2 l-1 .9 a6 6 0 0 0 2.6 2.6 l.9 -1 l2.2 .8 l0 1.5 a1.2 1.2 0 0 1 -1.3 1 a7 7 0 0 1 -6.6 -6.6 a1.2 1.2 0 0 1 .9 -1.4z" fill="currentColor"/></svg>
      </div>
      <div class="contact__line">maya@kelvadtrading.com.au
        <svg class="contact__icon" viewBox="0 0 20 20"><rect x="2.5" y="5" width="15" height="10.5" fill="none" stroke="currentColor" stroke-width="1.5"/><path d="M2.5 5 L10 11 L17.5 5" fill="none" stroke="currentColor" stroke-width="1.5"/></svg>
      </div>
      <div class="contact__line">www.heritagehollow.com.au
        <svg class="contact__icon" viewBox="0 0 20 20"><circle cx="10" cy="10" r="8" fill="none" stroke="currentColor" stroke-width="1.4"/><ellipse cx="10" cy="10" rx="3.5" ry="8" fill="none" stroke="currentColor" stroke-width="1.2"/><path d="M2 10 H18 M3.5 6 H16.5 M3.5 14 H16.5" stroke="currentColor" stroke-width="1.1"/></svg>
      </div>
    </address>
  </section>
</main>
</body>
</html>
```